Company director needs a business card design

I am a semi-retired former senior finance executive who sits on a number of public and private company boards and do some consulting work. I work largely with emerging businesses but deal regularly with top end of town lawyers, bankers etc. I need a thoughtful but relatively conservative design which would also resonate with my younger client base. Some colour would be good. Information limited to name, address, office tel, mobile and email.

Finance

```html
<!DOCTYPE html>
<html lang="en">
<head>
<meta charset="utf-8">
<title>Marcus Hale – Business Card</title>
<link href="https://fonts.googleapis.com/css2?family=Exo+2:wght@400;500;600&display=swap" rel="stylesheet">
<style>
  :root {
    --page-bg: #e4e4e4;
    --card-bg: #222222;
    --band-bg: #ffffff;
    --ink-light: #ffffff;
    --ink-dark: #222222;
  }
  * { box-sizing: border-box; margin: 0; padding: 0; }
  html, body {
    width: 992px;
    height: 1200px;
    overflow: hidden;
    background: var(--page-bg);
    font-family: "Exo 2", "Segoe UI", sans-serif;
  }
  .business-card {
    position: absolute;
    left: 67px;
    top: 330px;
    width: 861px;
    height: 491px;
    border-radius: 22px;
    background: var(--card-bg);
    color: var(--ink-light);
    overflow: hidden;
  }
  .holder-name {
    position: absolute;
    left: 50px;
    top: 92px;
    font-size: 34px;
    font-weight: 500;
    letter-spacing: 0.2px;
    line-height: 1;
  }
  .holder-role {
    position: absolute;
    left: 50px;
    top: 131px;
    font-size: 17px;
    font-weight: 400;
    line-height: 1;
  }
  .address-band {
    position: absolute;
    left: 0;
    top: 235px;
    width: 100%;
    height: 50px;
    background: var(--band-bg);
    color: var(--ink-dark);
    font-size: 21px;
    letter-spacing: 0.9px;
    display: flex;
    align-items: center;
    padding-left: 50px;
    white-space: nowrap;
  }
  .contact-list {
    position: absolute;
    left: 49px;
    top: 311px;
    list-style: none;
  }
  .contact-item {
    display: flex;
    align-items: center;
    height: 33px;
    font-size: 20px;
    letter-spacing: 0.3px;
    white-space: nowrap;
  }
  .contact-icon {
    width: 22px;
    height: 22px;
    margin-right: 14px;
    flex: none;
  }
</style>
</head>
<body>
  <section class="business-card">
    <h1 class="holder-name">MARCUS HALE</h1>
    <p class="holder-role">Company Director</p>

    <div class="address-band">Hale Advisory 18 Elm Street Dunmore, VT 05733</div>

    <ul class="contact-list">
      <li class="contact-item">
        <svg class="contact-icon" viewBox="0 0 22 22" aria-hidden="true">
          <rect x="4" y="1.5" width="14" height="19" rx="2.5" fill="none" stroke="#fff" stroke-width="2"/>
          <rect x="9" y="16.5" width="4" height="1.5" fill="#fff"/>
        </svg>
        <span>0455 2817 604</span>
      </li>
      <li class="contact-item">
        <svg class="contact-icon" viewBox="0 0 22 22" aria-hidden="true">
          <rect x="5" y="2" width="12" height="18" fill="#fff"/>
          <g fill="#222">
            <rect x="7.5" y="4.5" width="2.5" height="2.5"/><rect x="12" y="4.5" width="2.5" height="2.5"/>
            <rect x="7.5" y="9" width="2.5" height="2.5"/><rect x="12" y="9" width="2.5" height="2.5"/>
            <rect x="7.5" y="13.5" width="2.5" height="2.5"/><rect x="12" y="13.5" width="2.5" height="2.5"/>
          </g>
          <rect x="2" y="19.5" width="18" height="2" fill="#fff"/>
        </svg>
        <span>0398 6142 370</span>
      </li>
      <li class="contact-item">
        <svg class="contact-icon" viewBox="0 0 22 22" aria-hidden="true">
          <rect x="1" y="5" width="20" height="13" fill="none" stroke="#fff" stroke-width="1.8"/>
          <path d="M1 5 L11 13 L21 5 M1 18 L8.5 11 M21 18 L13.5 11" fill="none" stroke="#fff" stroke-width="1.6"/>
        </svg>
        <span>www.haleadvisory.com</span>
      </li>
      <li class="contact-item">
        <svg class="contact-icon" viewBox="0 0 22 22" aria-hidden="true">
          <rect x="2" y="3" width="18" height="13" fill="none" stroke="#fff" stroke-width="2"/>
          <rect x="10" y="16" width="2" height="3" fill="#fff"/>
          <rect x="6" y="19" width="10" height="1.8" fill="#fff"/>
        </svg>
        <span>info@haleadvisory.com</span>
      </li>
    </ul>
  </section>
</body>
</html>
```